Business card - mobile service

O KiraLink is a mobile family safety service based on tablets and smartphones.
The business card must have:
BASIC INFO
Company Logo
Name
Position / Job Title: Co-founder
Mobile Phone Number: +55 (11) 5080 6192
Land Line: +55 (11) 8765 093412
Email Address: name@kiralink-example.com
Web Site URL: www.kiralink-example.com
PROMOTIONAL INFO
Try KiraLink free Today!
Your personal promo code: qqqq-5151-hhhh-3030-9876
Promo code text explanation with the instructions about the trial offer
Updates
Dears,
One more must have: the KiraLink slogan:
Industry/Entity Type
Safety
Look and feel
Each slider illustrates characteristics of the customer's brand and the style your logo design should communicate.

```html
<!DOCTYPE html>
<html lang="en">
<head>
<meta charset="utf-8">
<title>KiraLink Business Card</title>
<link rel="stylesheet" href="https://fonts.googleapis.com/css2?family=Open+Sans:wght@400;600;700&display=swap">
<style>
  :root {
    --brand-blue: #1ba3dd;
    --brand-yellow: #fccb16;
    --ink: #1e1e1e;
    --paper: #ffffff;
    --canvas: #ffffff;
    --card-shadow: rgba(0, 0, 0, 0.22);
  }
  * { box-sizing: border-box; margin: 0; padding: 0; }
  html, body {
    width: 1200px;
    height: 900px;
    overflow: hidden;
    background: var(--canvas);
    font-family: "Open Sans", Arial, sans-serif;
    color: var(--ink);
  }
  .stage { position: relative; width: 1200px; height: 900px; }

  .card {
    position: absolute;
    width: 650px;
    height: 398px;
    border-radius: 30px;
    overflow: hidden;
    box-shadow: 6px 8px 12px var(--card-shadow);
  }

  /* Back side */
  .card-back {
    left: 468px;
    top: 420px;
    background: var(--brand-yellow);
  }
  .back-wordmark {
    position: absolute;
    left: 34px;
    top: 78px;
    font-weight: 700;
    font-size: 96px;
    line-height: 0.86;
    letter-spacing: -3px;
    color: var(--brand-blue);
  }
  .promo {
    position: absolute;
    left: 320px;
    top: 122px;
    width: 300px;
    font-size: 16.5px;
    line-height: 24px;
    color: var(--ink);
  }
  .promo p + p { margin-top: 20px; }

  /* Front side */
  .card-front {
    left: 82px;
    top: 82px;
    background: var(--paper);
    border-radius: 0 30px 30px 30px;
  }
  .front-accent {
    position: absolute;
    left: -59px;
    top: 203px;
    width: 246px;
    height: 246px;
    border-radius: 50%;
    background: var(--brand-yellow);
  }
  .front-wordmark {
    position: absolute;
    left: 38px;
    top: 46px;
    font-weight: 700;
    font-size: 64px;
    line-height: 1;
    letter-spacing: -2px;
    color: var(--brand-blue);
  }
  .slogan {
    position: absolute;
    left: 178px;
    top: 138px;
    font-size: 14px;
    color: var(--ink);
  }
  .contact {
    position: absolute;
    left: 357px;
    top: 178px;
    font-size: 16.5px;
    line-height: 24px;
  }
  .person-name { font-size: 24px; font-weight: 700; line-height: 30px; }
  .person-role { font-size: 17px; margin-bottom: 16px; }
  .phones, .online { list-style: none; }
  .phones { margin-bottom: 20px; }
  .label { font-weight: 700; display: inline-block; }
  .phones .label { width: 85px; }
  .online .label { width: 20px; text-align: center; margin-right: 2px; }
</style>
</head>
<body>
  <main class="stage">
    <section class="card card-back" aria-label="Business card, back">
      <div class="back-wordmark">kira<br>link</div>
      <div class="promo">
        <p>Try KiraLink free Today!</p>
        <p>Your personal promo code<br>qqqq-5151-hhhh-3030-9876</p>
        <p>Promo code text explanation with<br>the instructions about the trial offer</p>
      </div>
    </section>

    <section class="card card-front" aria-label="Business card, front">
      <div class="front-accent"></div>
      <div class="front-wordmark">kiralink</div>
      <p class="slogan">Your Family Safety Service</p>
      <div class="contact">
        <h1 class="person-name">Rafael Duarte</h1>
        <p class="person-role">Co-founder</p>
        <ul class="phones">
          <li><span class="label">Land Line</span>+55 (11) 8765 093412</li>
          <li><span class="label">Mobile</span>+55 (11) 5080 6192</li>
        </ul>
        <ul class="online">
          <li><span class="label">e</span> name@kiralink-example.com</li>
          <li><span class="label">w</span> www.kiralink-example.com</li>
        </ul>
      </div>
    </section>
  </main>
</body>
</html>
```